I want ideas sample designs for my book cover

Hello,

We need a book cover designed in flat and 3D Versions. We would like to have jpg and png for final output and include a copy of the PSD for future revisions.

Here are the basic details:

Title: The Harvest of Quiet Builders
Author: Norman Quillfeather

Dimensions of book:

Was looking at the Pavo website for dimensions. I thought you may want to go on there and look at the different sizes. I used the 6x9” perfect bound US trade size for my book. You will see that this has a spine width of 0.225”, Cover size of 12.48 x 9.25” and spine begins at 6.125”

If you need background info on the author just to get an idea what he does, please check:

http://NormanQuillfeather.example

IMPORTANT: Please see attached document for a more detailed info:

Exact Title Of book
Back Cover
Spine Info
Measurements of book and dimension
Examples of book covers
Norman's photo attached

Thanks,
Darlene

Industry/Entity Type

Life Coaching

Font styles to use
Serif

Requirements
Must have
• Jpg, png and PSD files
• title
• author
• exact dimensions
• front and back cover
• flat and 3d versions

```html
<!DOCTYPE html>
<html lang="en">
<head>
<meta charset="utf-8">
<title>The Harvest of Quiet Builders – Cover Concepts</title>
<link href="https://fonts.googleapis.com/css2?family=Oswald:wght@500;700&family=Roboto+Condensed:wght@400;700&family=Open+Sans:wght@400&display=swap" rel="stylesheet">
<style>
  :root {
    --stage: #a4a4a4;
    --orange: #f26a1f;
    --lime: #a8d64a;
    --ink: #14141a;
    --navy: #1c2238;
    --white: #ffffff;
    --sky-top: #7fa6cf;
    --sky-mid: #dfe9f1;
    --sea: #2f5f94;
    --sea-deep: #183a66;
  }
  * { box-sizing: border-box; margin: 0; padding: 0; }
  html, body { width: 1200px; height: 1200px; overflow: hidden; background: var(--stage); }
  .stage { position: relative; width: 1200px; height: 1200px; }

  .cover {
    position: absolute; width: 272px; height: 520px; overflow: hidden;
    background: var(--ink);
    font-family: "Roboto Condensed", sans-serif;
    box-shadow: 0 6px 14px rgba(0,0,0,.25);
  }
  .photo { position: absolute; inset: 0; }
  .photo--day {
    background: linear-gradient(180deg, var(--sky-top) 0%, var(--sky-mid) 42%, #c9d8e6 55%, var(--sea) 64%, var(--sea-deep) 82%, #0f1a2a 100%);
  }
  .photo--dusk {
    background: linear-gradient(180deg, #1a2140 0%, #4b5c8c 35%, #b8c3d6 55%, #5a78a6 68%, #1a2238 100%);
  }
  .photo--warm {
    background: linear-gradient(180deg, #c9cdd3 0%, #f2d8b0 30%, #f6c489 45%, #9cb3c8 62%, var(--sea) 75%, var(--sea-deep) 100%);
  }
  .band { position: absolute; background: var(--ink); }

  .kicker { font-size: 11px; line-height: 1.2; }
  .author { font-weight: 700; line-height: 1; letter-spacing: -.2px; }
  .tagline { font-size: 12.5px; line-height: 1.35; }
  .title {
    font-family: "Oswald", sans-serif; font-weight: 700; text-transform: uppercase;
    line-height: .98; letter-spacing: -.5px;
  }
  .title .the { font-size: .55em; text-transform: none; font-weight: 500; margin-right: 4px; }

  .num {
    position: absolute; width: 272px; text-align: center;
    font-family: "Open Sans", sans-serif; font-size: 46px; color: #111; line-height: 1;
  }

  /* concept 1 */
  .c1 { left: 56px; top: 34px; }
  .c1 .band { left: 0; right: 0; bottom: 0; height: 150px; }
  .c1 .kicker { position: absolute; top: 22px; left: 40px; color: var(--ink); }
  .c1 .author { position: absolute; top: 40px; left: 36px; font-size: 29px; color: var(--orange); }
  .c1 .tagline { position: absolute; top: 232px; left: 50px; width: 180px; text-align: center; color: var(--white); font-size: 11.5px; }
  .c1 .title { position: absolute; left: 20px; bottom: 30px; color: var(--orange); font-size: 34px; }

  /* concept 2 */
  .c2 { left: 432px; top: 34px; }
  .c2 .kicker { position: absolute; top: 24px; left: 42px; color: var(--lime); }
  .c2 .author { position: absolute; top: 46px; left: 60px; font-size: 22px; color: var(--white); font-weight: 400; }
  .c2 .tagline { position: absolute; top: 136px; right: 18px; width: 130px; text-align: right; color: var(--ink); }
  .c2 .title { position: absolute; left: 24px; top: 310px; color: var(--lime); font-size: 33px; }

  /* concept 3 */
  .c3 { left: 828px; top: 34px; }
  .c3 .band { left: 0; top: 0; bottom: 0; width: 96px; background: rgba(20,20,26,.92); }
  .c3 .title {
    position: absolute; left: 14px; bottom: 60px; transform-origin: left bottom; transform: rotate(-90deg) translateY(100%);
    color: var(--orange); font-family: "Roboto Condensed", sans-serif; font-size: 36px; width: 460px; line-height: 1;
  }
  .c3 .tagline { position: absolute; top: 110px; right: 20px; width: 110px; text-align: right; color: var(--ink); font-size: 13px; }
  .c3 .kicker { position: absolute; bottom: 60px; right: 20px; color: var(--white); font-size: 9px; }
  .c3 .author { position: absolute; bottom: 30px; right: 20px; font-size: 21px; color: var(--white); }

  /* concept 4 */
  .c4 { left: 56px; top: 618px; }
  .c4 .band { left: 0; bottom: 0; width: 150px; height: 220px; background: linear-gradient(90deg, var(--ink) 70%, rgba(20,20,26,0)); }
  .c4 .kicker { position: absolute; top: 176px; left: 104px; color: var(--ink); font-size: 10px; }
  .c4 .author { position: absolute; top: 194px; left: 102px; font-size: 22px; color: var(--ink); }
  .c4 .title { position: absolute; left: 18px; top: 236px; color: var(--orange); font-size: 31px; }
  .c4 .tagline { position: absolute; left: 18px; top: 368px; width: 140px; color: var(--white); font-size: 11.5px; }

  /* concept 5 */
  .c5 { left: 432px; top: 618px; }
  .c5 .band { left: 0; right: 0; bottom: 0; height: 190px; background: linear-gradient(180deg, rgba(20,20,26,.85), var(--ink) 40%); }
  .c5 .kicker { position: absolute; top: 30px; left: 20px; color: var(--ink); }
  .c5 .author { position: absolute; top: 48px; left: 20px; font-size: 25px; color: var(--orange); }
  .c5 .tagline { position: absolute; top: 126px; left: 20px; width: 130px; color: var(--ink); font-size: 11.5px; }
  .c5 .title { position: absolute; left: 16px; bottom: 44px; color: var(--orange); font-size: 34px; }

  /* concept 6 */
  .c6 { left: 828px; top: 618px; }
  .c6 .band { right: 0; top: 270px; bottom: 0; width: 170px; background: linear-gradient(90deg, rgba(20,20,26,0), var(--ink) 30%); }
  .c6 .tagline { position: absolute; top: 48px; left: 16px; width: 110px; color: var(--ink); font-size: 12px; }
  .c6 .title { position: absolute; left: 16px; top: 254px; color: var(--orange); font-size: 33px; }
  .c6 .kicker { position: absolute; bottom: 72px; right: 16px; color: var(--white); font-size: 10px; }
  .c6 .author { position: absolute; bottom: 40px; right: 16px; font-size: 22px; color: var(--orange); }
</style>
</head>
<body>
<main class="stage">

  <section class="cover c1">
    <div class="photo photo--day" role="img" aria-label="Photo of a man in a suit seen from behind, looking out over the ocean"></div>
    <div class="band"></div>
    <p class="kicker">From the Best Selling Author of “<b>Lanterns</b>”</p>
    <p class="author">Norman Quillfeather</p>
    <p class="tagline">How this ANCIENT WISDOM is HELPING billionaires, industry icons and entrepreneurs TO BE BETTER LEADERS, increase impact and leave a legacy</p>
    <h2 class="title"><span class="the">The</span>Harvest of<br>Quiet Builders</h2>
  </section>
  <div class="num" style="left:56px;top:560px">1</div>

  <section class="cover c2">
    <div class="photo photo--dusk" role="img" aria-label="Photo of a man in a suit seen from behind at dusk, facing the sea"></div>
    <p class="kicker">From the Best Selling Author of “Lanterns”</p>
    <p class="author">Norman Quillfeather</p>
    <p class="tagline">How this ancient wisdom is helping billionaires, industry icons and entrepreneurs to be better leaders, increase impact and leave a legacy</p>
    <h2 class="title"><span class="the">The</span>Harvest of<br>Quiet Builders</h2>
  </section>
  <div class="num" style="left:432px;top:560px">2</div>

  <section class="cover c3">
    <div class="photo photo--day" role="img" aria-label="Close photo of a man in a suit seen from behind, looking at the ocean"></div>
    <div class="band"></div>
    <h2 class="title"><span class="the">The</span> Harvest of<br>Quiet Builders</h2>
    <p class="tagline">How this ANCIENT WISDOM is helping billionaires, INDUSTRY ICONS and entrepreneurs to be better LEADERS, increase impact and leave A LEGACY</p>
    <p class="kicker">From the Best Selling Author of “<b>Lanterns</b>”</p>
    <p class="author">Norman Quillfeather</p>
  </section>
  <div class="num" style="left:828px;top:560px">3</div>

  <section class="cover c4">
    <div class="photo photo--warm" role="img" aria-label="Photo of a man in a suit in profile against a warm sky over breaking waves"></div>
    <div class="band"></div>
    <p class="kicker">From the Best Selling Author of “Lanterns”</p>
    <p class="author">Norman<br>Quillfeather</p>
    <h2 class="title"><span class="the">The</span>Harvest of<br>Quiet Builders</h2>
    <p class="tagline">How this ancient wisdom is helping billionaires, industry icons and entrepreneurs to be better leaders, increase impact and leave a legacy</p>
  </section>
  <div class="num" style="left:56px;top:1146px">4</div>

  <section class="cover c5">
    <div class="photo photo--day" role="img" aria-label="Photo of a man in a suit seen from behind, facing the surf"></div>
    <div class="band"></div>
    <p class="kicker">From the Best Selling Author of “Lanterns”</p>
    <p class="author">Norman Quillfeather</p>
    <p class="tagline">How this ancient wisdom is helping billionaires, industry icons and entrepreneurs to be better leaders, increase impact and leave a legacy</p>
    <h2 class="title"><span class="the">The</span>Harvest of<br>Quiet Builders</h2>
  </section>
  <div class="num" style="left:432px;top:1146px">5</div>

  <section class="cover c6">
    <div class="photo photo--day" role="img" aria-label="Photo of a man in a suit seen from behind, looking at the sea under a pale sky"></div>
    <div class="band"></div>
    <p class="tagline">How this ancient wisdom is helping billionaires, industry icons and entrepreneurs to be better leaders, increase impact and leave a legacy</p>
    <h2 class="title"><span class="the">The</span>Harvest of<br>Quiet Builders</h2>
    <p class="kicker">From the Best Selling Author of “Lanterns”</p>
    <p class="author">Norman Quillfeather</p>
  </section>
  <div class="num" style="left:828px;top:1146px">6</div>

</main>
</body>
</html>
```